Classy, Elegant, Simple Business Card Design

Looking to have a classy, simple, and elegant design. Want a top notch designed business card. I really like the look of the new torvane credit card. I also like the design I attached. I am trying to reach 21-29 year old females for booking us for there wedding or event. We offer Disc Jockey Service, Photo Booth Rentals, and Uplighting .

Target Market(s)

21-28 year old females

Contact Information for Business Card

Has to have logo, website, email, and phone number

Font styles to use
Other font styles liked:
• open to font choice, modern, clean
Designer to choose
33a6d7
0791cd
0555a3
ffffff

Requirements
Must have
• Has to have logo, website, email, and phone number
Nice to have
• I really like the design of the new torvane credit card. I also included my logo and some designs I like
Should not have
• clutter or too much info

```html
<!DOCTYPE html>
<html lang="en">
<head>
<meta charset="utf-8">
<title>Tidecrest Event Group – Business Card</title>
<link href="https://fonts.googleapis.com/css2?family=Poppins:wght@400;500&display=swap" rel="stylesheet">
<style>
  :root {
    --stage: #1d1d1d;
    --paper: #ffffff;
    --blue: #0791cd;
    --blue-deep: #0555a3;
    --blue-light: #33a6d7;
    --ink: #3a3a3a;
    --muted: #8a8a8a;
    --rule: #555555;
    --silver: #b3b3b3;
  }
  html, body {
    margin: 0;
    width: 1200px;
    height: 1200px;
    overflow: hidden;
    background: var(--stage);
    font-family: "Poppins", sans-serif;
  }
  .canvas { position: relative; width: 1200px; height: 1200px; }
  .card {
    position: absolute;
    left: 257px;
    width: 686px;
    height: 392px;
    overflow: hidden;
  }
  .card--front { top: 165px; background: var(--paper); }
  .card--back {
    top: 653px;
    background: radial-gradient(ellipse at 50% 45%, #0aa6e2 0%, var(--blue) 45%, #137fc6 100%);
  }
  .brand {
    position: absolute;
    right: 42px;
    top: 62px;
    text-align: center;
    color: var(--blue-deep);
    font-weight: 500;
  }
  .brand__name { font-size: 30px; letter-spacing: 1px; line-height: 1.1; }
  .brand__sub { font-size: 11px; letter-spacing: 6px; margin-top: 4px; }
  .person { position: absolute; left: 37px; top: 248px; }
  .person__name { margin: 0; font-size: 22px; font-weight: 500; color: var(--blue); line-height: 1.2; }
  .person__role { margin: 0; font-size: 15px; color: var(--muted); }
  .divider {
    position: absolute; left: 37px; width: 607px; top: 305px;
    height: 1px; background: var(--rule);
  }
  .contact { position: absolute; left: 37px; top: 317px; list-style: none; margin: 0; padding: 0; }
  .contact li { display: flex; align-items: center; gap: 8px; font-size: 15.5px; color: var(--ink); line-height: 20px; }
  .contact svg { width: 13px; height: 13px; fill: var(--blue); }
  .footer-band { position: absolute; left: 0; bottom: 0; width: 686px; height: 29px; }
  .website {
    position: absolute; right: 34px; bottom: 4px;
    color: var(--paper); font-size: 15.5px;
  }
  .back-brand {
    position: absolute; left: 0; right: 0; top: 150px;
    text-align: center; color: var(--blue-deep);
    font-size: 56px; font-weight: 500; letter-spacing: 2px;
  }
  .services {
    position: absolute; left: 0; right: 0; top: 338px;
    text-align: center; color: var(--paper);
    font-size: 15.5px; font-weight: 500;
  }
</style>
</head>
<body>
<main class="canvas">
  <section class="card card--front">
    <div class="brand">
      <div class="brand__name">TIDECREST</div>
      <div class="brand__sub">EVENT GROUP</div>
    </div>

    <div class="person">
      <h1 class="person__name">Daniel Brooks</h1>
      <p class="person__role">President</p>
    </div>

    <div class="divider"></div>

    <ul class="contact">
      <li>
        <svg viewBox="0 0 24 24" aria-hidden="true"><path d="M6.6 10.8a15.2 15.2 0 0 0 6.6 6.6l2.2-2.2a1 1 0 0 1 1-.25 11.4 11.4 0 0 0 3.6.57 1 1 0 0 1 1 1V20a1 1 0 0 1-1 1A17 17 0 0 1 3 4a1 1 0 0 1 1-1h3.5a1 1 0 0 1 1 1c0 1.25.2 2.45.57 3.57a1 1 0 0 1-.25 1z"/></svg>
        555-014-2870
      </li>
      <li>
        <svg viewBox="0 0 24 24" aria-hidden="true"><path d="M2 5h20v14H2z M3.5 6.5 12 13l8.5-6.5" fill="var(--blue)"/><path d="M3 6.5 12 13l9-6.5" fill="none" stroke="#fff" stroke-width="1.6"/></svg>
        hello@tidecrestevents.com
      </li>
    </ul>

    <svg class="footer-band" viewBox="0 0 686 29" preserveAspectRatio="none" aria-hidden="true">
      <rect x="0" y="14" width="686" height="6" fill="var(--silver)"/>
      <rect x="0" y="20" width="686" height="9" fill="var(--blue)"/>
      <path d="M420 20 C 450 20, 460 0, 500 0 L686 0 L686 29 L0 29 L0 20 Z" fill="var(--blue)"/>
    </svg>
    <div class="website">www.tidecrestevents.com</div>
  </section>

  <section class="card card--back">
    <div class="back-brand">TIDECREST</div>
    <p class="services">Disc Jockey Service • Photo Booth Rentals • Uplighting .</p>
  </section>
</main>
</body>
</html>
```